Business card for Eyelash extension salon in Linden Park,California USA

We need new business card for our salon in Linden Park. The salon name is 'Lashvera' . We would like to have...Business name: Lashvera Name of person: will provide later Address 4720 N.Alder Crest Ave Linden Park , CA 90412 Phone: will provide later (Text only) Web: www.lashverastudio.example Snapgrid icon, Circlebook icon follow us for seasonal campaign and news @lashverastudiolounge Design should look elegant, high-end, clean, simple, cohesive with my brand. Please refer my brand board. Business name color will be metallic bronzy color. Im thinking grey background or white background. Thanks

Target Market(s)

25-35. Gender neutral. People who are in Entertainment business industry.
This is High-end Eyelash extension salon in Linden Park

Industry/Entity Type

Beauty Salon

Contact Information for Business Card

Business name: Lashvera
Name of person: will provide later
Address 4720 N.Alder Crest Ave Linden Park , CA 90412
Phone: will provide later (Text only)
Web: www.lashverastudio.example
Snapgrid icon, Circlebook icon
follow us for seasonal campaign and news @lashverastudiolounge

Requirements
Must have
• Beautiful, elegant, clean and simple look but very attractive and modern
Should not have
• We don't like too clutter, too busy designs.

```html
<!DOCTYPE html>
<html lang="en">
<head>
<meta charset="utf-8">
<title>Lashvera – Business Card</title>
<link rel="stylesheet" href="https://fonts.googleapis.com/css2?family=Bodoni+Moda:wght@700&family=Poppins:ital,wght@0,300;0,400;0,500;1,600&display=swap">
<style>
  :root {
    --backdrop: #2b2c30;
    --peach: #dcae8a;
    --peach-light: #e4bb99;
    --bronze: #a46c56;
    --marble-light: #f7f7f7;
    --marble-mid: #e6e6e8;
    --ink: #111111;
    --ink-soft: #2a2a2a;
  }
  * { margin: 0; padding: 0; box-sizing: border-box; }
  html, body {
    width: 1200px; height: 900px; overflow: hidden;
    background: var(--backdrop);
    font-family: "Poppins", sans-serif;
  }
  .stage { position: relative; width: 1200px; height: 900px; }

  .card {
    position: absolute;
    top: 301px;
    width: 520px; height: 297px;
    border-radius: 3px;
    overflow: hidden;
    box-shadow: 0 18px 40px rgba(0,0,0,.45);
  }

  /* Back: contact side */
  .card--back { left: 50px; }
  .marble-surface {
    position: absolute; inset: 0;
    background:
      radial-gradient(ellipse at 30% 30%, var(--marble-light) 0%, transparent 60%),
      radial-gradient(ellipse at 75% 70%, #efeff0 0%, transparent 55%),
      linear-gradient(135deg, var(--marble-light), var(--marble-mid));
  }
  .back-content {
    position: absolute; inset: 0;
    padding: 38px 40px 0 44px;
    color: var(--ink);
  }
  .person-name {
    font-family: "Bodoni Moda", serif;
    font-weight: 700;
    font-size: 21px;
    letter-spacing: 0.5px;
    text-align: center;
    padding-left: 150px;
  }
  .contact-row {
    display: flex; align-items: center;
    margin-top: 24px;
    font-size: 13.5px; line-height: 1.3;
    color: var(--ink-soft);
  }
  .contact-col { flex: 0 0 auto; }
  .contact-col--reach { width: 205px; }
  .divider {
    width: 1.5px; height: 50px;
    background: var(--ink);
    margin: 0 22px 0 14px;
  }
  .follow-line {
    margin-top: 30px;
    font-size: 13px; font-weight: 600; font-style: italic;
  }
  .social-row {
    display: flex; align-items: center; gap: 10px;
    margin-top: 10px;
    font-size: 13.5px; font-weight: 500;
  }
  .social-item { display: flex; align-items: center; gap: 6px; }
  .social-dot { width: 14px; height: 14px; border-radius: 50%; background: var(--ink); }

  /* Front: brand side */
  .card--front {
    left: 630px;
    background: linear-gradient(135deg, var(--peach-light), var(--peach));
    display: flex; flex-direction: column; align-items: center; justify-content: center;
  }
  .brand-name {
    font-family: "Poppins", sans-serif;
    font-weight: 300;
    font-size: 60px;
    letter-spacing: 4px;
    color: var(--bronze);
    line-height: 1.1;
  }
  .brand-location {
    margin-top: 10px;
    font-size: 11px;
    font-weight: 400;
    letter-spacing: 3px;
    color: var(--bronze);
    opacity: .85;
  }
</style>
</head>
<body>
<main class="stage">
  <section class="card card--back">
    <div class="marble-surface" role="img" aria-label="White marble texture with soft grey veining"></div>
    <div class="back-content">
      <h1 class="person-name">JORDAN AVERY</h1>
      <div class="contact-row">
        <div class="contact-col contact-col--reach">
          <p>555 014 2783 (Text only)</p>
          <p>www.lashverastudio.example</p>
        </div>
        <div class="divider"></div>
        <div class="contact-col contact-col--address">
          <p>4720 N.Alder Crest Ave,</p>
          <p>Linden Park , CA 90412</p>
        </div>
      </div>
      <p class="follow-line">Follow us for seasonal campaign and news</p>
      <div class="social-row">
        <span class="social-item"><span class="social-dot"></span>Circlebook</span>
        <span class="social-handle">@lashverastudiolounge</span>
        <span class="social-item"><span class="social-dot"></span>Snapgrid</span>
      </div>
    </div>
  </section>

  <section class="card card--front">
    <p class="brand-name">Lashvera</p>
    <p class="brand-location">LINDEN PARK</p>
  </section>
</main>
</body>
</html>
```